Harborlight Amusement Collective (HAC)

We need a business card design for Harborlight Amusement Collective. Modern and sleek looking, with all critical information. Open to single or double sided designs, if double sided info needs to be all on one side. The main Logo is Harborlight Amusement collective and must be on the card. The other three logos are for the brands that fall under the group, they might be good on the back.

Industry/Entity Type

Business

```html
<!DOCTYPE html>
<html lang="en">
<head>
<meta charset="utf-8">
<title>Harborlight Amusement Collective – Business Card</title>
<link href="https://fonts.googleapis.com/css2?family=Montserrat:wght@400;500;600;700&family=Roboto+Condensed:wght@700&display=swap" rel="stylesheet">
<style>
  :root {
    --bg: #d6d6d6;
    --card: #ffffff;
    --blue: #2353a3;
    --green: #8aa83a;
    --ink: #2a2a2a;
    --muted: #555555;
  }
  * { box-sizing: border-box; margin: 0; padding: 0; }
  html, body { width: 1200px; height: 852px; overflow: hidden; }
  body {
    background: var(--bg);
    font-family: "Montserrat", sans-serif;
    color: var(--ink);
    position: relative;
  }
  .card {
    position: absolute;
    width: 540px;
    height: 310px;
    background: var(--card);
    border-radius: 22px;
    box-shadow: 0 10px 24px rgba(0,0,0,.22);
    overflow: hidden;
  }
  .card--brands { left: 40px; top: 271px; }
  .card--contact { left: 620px; top: 271px; }

  /* wordmark */
  .wordmark { display: flex; align-items: center; gap: 12px; }
  .wordmark__square { width: 34px; height: 34px; background: var(--blue); flex: none; }
  .wordmark__name {
    color: var(--blue);
    font-weight: 700;
    font-size: 17px;
    line-height: 1.2;
    letter-spacing: .04em;
    text-transform: uppercase;
    white-space: nowrap;
  }

  .rule { position: absolute; height: 2px; }
  .rule--green { background: var(--green); opacity: .7; }
  .rule--blue { background: var(--blue); }

  /* brands side */
  .card--brands .wordmark { position: absolute; left: 0; right: 0; top: 50px; justify-content: center; }
  .card--brands .rule--blue { left: 150px; width: 240px; top: 112px; }
  .brands__rule-top { left: 40px; width: 460px; top: 158px; }
  .brands__rule-bottom { left: 40px; width: 460px; top: 220px; }
  .brands__label {
    position: absolute; left: 0; right: 0; top: 136px;
    text-align: center; font-size: 13px; color: var(--muted);
  }
  .brands__list {
    position: absolute; left: 20px; right: 20px; top: 170px;
    display: flex; justify-content: space-around; align-items: center;
  }
  .brand { font-size: 17px; font-weight: 600; color: var(--blue); padding: 0 10px; white-space: nowrap; }
  .brand + .brand { border-left: 1px solid #c8c8c8; }
  .brands__web {
    position: absolute; left: 0; right: 0; top: 240px;
    text-align: center; font-size: 14px; color: var(--ink);
  }
  .brands__web span { color: var(--blue); }

  /* contact side */
  .card--contact .wordmark { position: absolute; right: 30px; top: 44px; }
  .card--contact .rule--blue { right: 30px; width: 230px; top: 100px; }
  .person { position: absolute; left: 40px; top: 118px; }
  .person__name {
    font-family: "Roboto Condensed", sans-serif;
    font-weight: 700; font-size: 26px; color: var(--blue);
  }
  .person__role { font-size: 14px; margin-top: 4px; }
  .contact__list { position: absolute; left: 40px; top: 198px; list-style: none; font-size: 14px; }
  .contact__list li { display: flex; align-items: center; gap: 10px; height: 22px; }
  .contact__list svg { width: 12px; height: 12px; fill: var(--blue); flex: none; }
  .contact__list .web { color: var(--blue); }
</style>
</head>
<body>

  <section class="card card--brands" aria-label="Card back – group brands">
    <div class="wordmark">
      <span class="wordmark__square" aria-hidden="true"></span>
      <span class="wordmark__name">Harborlight Amusement<br>Collective</span>
    </div>
    <div class="rule rule--blue"></div>
    <p class="brands__label">Our Brands</p>
    <div class="rule rule--green brands__rule-top"></div>
    <div class="brands__list">
      <span class="brand">Quayside Tickets</span>
      <span class="brand">Boardwalk Hospitality</span>
      <span class="brand">Gatepass</span>
    </div>
    <div class="rule rule--green brands__rule-bottom"></div>
    <p class="brands__web">www.<span>harborlightcollective</span>.com</p>
  </section>

  <section class="card card--contact" aria-label="Card front – contact details">
    <div class="wordmark">
      <span class="wordmark__square" aria-hidden="true"></span>
      <span class="wordmark__name">Harborlight Amusement<br>Collective</span>
    </div>
    <div class="rule rule--blue"></div>
    <div class="person">
      <h1 class="person__name">Alex Morgan Reed</h1>
      <p class="person__role">Managing Director</p>
    </div>
    <ul class="contact__list">
      <li><svg viewBox="0 0 24 24" aria-hidden="true"><path d="M6.6 10.8a15 15 0 0 0 6.6 6.6l2.2-2.2c.3-.3.7-.4 1-.2 1.1.4 2.3.6 3.6.6.6 0 1 .4 1 1V20c0 .6-.4 1-1 1A17 17 0 0 1 3 4c0-.6.4-1 1-1h3.5c.6 0 1 .4 1 1 0 1.3.2 2.5.6 3.6.1.3 0 .7-.2 1z"/></svg>555.555.5555</li>
      <li><svg viewBox="0 0 24 24" aria-hidden="true"><path d="M2 5h20v14H2zm2 2v.5l8 5 8-5V7z"/></svg>alexreed@yourwebsite.com</li>
      <li><svg viewBox="0 0 24 24" aria-hidden="true"><circle cx="12" cy="12" r="10"/></svg><span>www.<span class="web">yourwebsite</span>.com</span></li>
      <li>234 Anywhere St., Any Town, US 123456</li>
    </ul>
  </section>

</body>
</html>
```